TuneRoost - Music Industry App needs a top quality wordpress homepage

We need a modern responsive wordpress homepage built. Our website will only feature one page with the goal to get people to sign up to our app. A word document has been uploaded outlining the page content/sections.

Once the homepage is finalised, I will also need 2 landing pages built as part of this competition. It will be very similar to the homepage with the same layout etc but just feature different images and content. The homepage is for anyone (artists and venues) to find out about us but the landing pages will be artist or venue specific.

The completed work must be delivered as an exportable file into wordpress and be designed properly so no more work is needed to begin utilising as the actual website. The images used must be setup correctly for speed and quality also.

Target Market(s)

Venues and Artists.

Coding

Coded - Design and coding required

Requirements
Must have
• UPDATE: High Res Logo files attached
• Must be a modern looking website and be responsive. Must look good across all devices from desktop, to mobile and tablet. Needs to be very high quality.
• Please see the attached logo - I am waiting for the final high quality version and will reupload when complete but this will be enough to get you started for now. The website must have a dark base colour and have red/white elements to match the logo. The red colour used MUST match the red colour used in the logo.
• Please have a go at creating it how you think is best and provide feedback from there. I am leaving it very open to the designers so I can get the best website possible and lots of different ideas etc.

```html
<!DOCTYPE html>
<html lang="en">
<head>
<meta charset="utf-8">
<title>TuneRoost – Live Music Booking</title>
<link href="https://fonts.googleapis.com/css2?family=Raleway:wght@300;400;500;600;700;800&display=swap" rel="stylesheet">
<style>
:root{
  --red:#e0141e;
  --red-dark:#a50c14;
  --ink:#161616;
  --ink-2:#1d1d1d;
  --white:#ffffff;
  --grey:#6b6b6b;
  --line:#cfcfcf;
}
*{box-sizing:border-box;margin:0;padding:0}
html,body{width:1200px;height:3885px;overflow:hidden}
body{position:relative;font-family:'Raleway',sans-serif;color:var(--grey);background:var(--white)}
.abs{position:absolute}
.red{color:var(--red)}
.light{font-weight:300}

/* nav */
.site-nav{position:absolute;left:0;top:0;width:1200px;height:104px;background:var(--ink)}
.nav-link{position:absolute;top:44px;font-size:12.5px;font-weight:500;color:#fff;letter-spacing:.3px;text-transform:uppercase}
.brand{position:absolute;left:600px;top:52px;transform:translate(-50%,-50%);display:flex;align-items:center;gap:8px;font-size:22px;font-weight:600;color:var(--white)}
.brand-dot{width:14px;height:14px;border-radius:50%;background:var(--red)}

/* hero */
.hero{position:absolute;left:0;top:104px;width:1200px;height:561px;
  background:radial-gradient(ellipse 420px 360px at 840px 240px,#7a3a78 0%,transparent 70%),
  radial-gradient(ellipse 300px 240px at 1120px 260px,#b0283c 0%,transparent 70%),
  linear-gradient(100deg,#1d0f2a 0%,#3c1a4a 45%,#6a2550 75%,#8a2238 100%)}
.hero h1{position:absolute;left:80px;top:150px;font-size:40px;font-weight:500;color:#fff;letter-spacing:-.3px}
.hero .lead{position:absolute;left:80px;top:218px;width:420px;font-size:17.5px;line-height:29px;color:#fff}
.hero .cta-text{position:absolute;left:80px;top:302px;font-size:17px;color:var(--red)}

/* pill form */
.pill-form{position:absolute;height:46px;border-radius:23px;background:#fff;border:1.5px solid #d6d6d6}
.pill-form.on-dark{border:3px solid #fff}
.pill-form .ph{position:absolute;left:22px;top:50%;transform:translateY(-50%);font-size:12.5px;color:#666}
.pill-form .btn{position:absolute;right:2px;top:2px;bottom:2px;width:136px;border-radius:21px;background:var(--red);color:#fff;font-size:15px;font-weight:500;display:flex;align-items:center;justify-content:center}

/* sections */
.section-title{position:absolute;left:0;width:1200px;text-align:center;font-size:37px;font-weight:800;color:var(--red)}
.section-title .light{font-weight:300}

.steps-line{position:absolute;left:0;top:780px}
.step-num{position:absolute;width:84px;height:84px;border-radius:50%;background:linear-gradient(135deg,var(--red) 50%,#c10f18 50%);color:#fff;font-size:29px;font-weight:500;display:flex;align-items:center;justify-content:center;box-shadow:0 6px 12px rgba(0,0,0,.18)}
.step-text{position:absolute;width:190px;text-align:center;font-size:13.5px;line-height:25px;color:#666}

.why{position:absolute;left:0;top:1093px;width:1200px;height:521px;background:var(--ink-2)}
.why-item h3{position:absolute;font-size:20px;font-weight:500;color:#fff}
.why-item p{position:absolute;width:230px;font-size:13px;line-height:25px;color:#ddd}
.why-item .right{text-align:right}
.why-icon{position:absolute;width:62px;height:62px;border-radius:50%;border:2px solid var(--red);display:flex;align-items:center;justify-content:center}
.why-badge{position:absolute;left:460px;top:1240px;width:280px;height:280px;border-radius:50%;
  background:radial-gradient(circle at 50% 40%,#3a2a2a 0%,#1a1414 70%,#0e0e0e 100%);box-shadow:0 10px 40px rgba(0,0,0,.6)}

.frame{position:absolute;background:var(--red)}
.photo{position:absolute}
.feature h2{position:absolute;font-size:33px;font-weight:700;color:var(--red)}
.bullets{position:absolute;list-style:none;width:490px}
.bullets li{position:relative;padding-left:20px;font-size:13.5px;line-height:25px;color:#666;margin-bottom:14px}
.bullets li::before{content:"";position:absolute;left:0;top:9px;width:7px;height:7px;border-radius:50%;background:var(--red)}
.body-copy{position:absolute;font-size:13px;line-height:25px;color:#777}

.about{position:absolute;left:0;top:2769px;width:1200px;height:280px;background:var(--ink-2)}
.about h2{position:absolute;left:80px;top:65px;font-size:38px;font-weight:800;color:var(--red)}
.about .intro{position:absolute;left:80px;top:135px;width:490px;font-size:15.5px;line-height:27px;color:#eee}
.about .more{position:absolute;left:638px;top:80px;width:490px;font-size:13px;line-height:25px;color:#ddd}

.field{position:absolute;border:1.5px solid #cfcfcf;border-radius:23px;font-size:13px;color:#777;padding:14px 22px}
.submit{position:absolute;left:517px;top:3360px;width:166px;height:45px;border-radius:23px;background:var(--red);color:#fff;font-size:17px;font-weight:600;display:flex;align-items:center;justify-content:center}

.footer{position:absolute;left:0;top:3478px;width:1200px;height:342px;background:var(--ink-2);text-align:center;color:#fff}
.footer .blurb{position:absolute;left:0;top:140px;width:1200px;font-size:16px;line-height:28px}
.call{position:absolute;left:0;top:225px;width:1200px;display:flex;align-items:center;justify-content:center;gap:18px;font-size:30px;font-weight:700}
.call .ring{width:56px;height:56px;border-radius:50%;border:2px solid #fff;display:flex;align-items:center;justify-content:center}
.copyright{position:absolute;left:0;top:3820px;width:1200px;height:65px;background:#0c0c0c;color:#ccc;font-size:12.5px;text-align:center;line-height:65px}
</style>
</head>
<body>

<header class="site-nav">
  <span class="nav-link" style="left:250px">How it works?</span>
  <span class="nav-link" style="left:380px">Venues</span>
  <span class="nav-link" style="left:457px">Artist</span>
  <div class="brand"><span class="brand-dot"></span>TuneRoost</div>
  <span class="nav-link" style="left:710px">Why TuneRoost</span>
  <span class="nav-link" style="left:825px">About</span>
  <span class="nav-link" style="left:897px">Contact</span>
</header>

<section class="hero" role="img" aria-label="Singer performing on stage under purple and red lights">
  <h1>ZIPRIDE FOR LIVE MUSIC</h1>
  <p class="lead">TuneRoost connects venues with artists to make booking gigs simple</p>
  <p class="cta-text">Sign up now for FREE</p>
  <div class="pill-form on-dark" style="left:78px;top:360px;width:395px"><span class="ph">Enter your email</span><span class="btn">SIGN UP</span></div>
</section>

<h2 class="section-title" style="top:712px">How TuneRoost <span class="light">Works</span></h2>
<svg class="abs" style="left:0;top:780px" width="1200" height="180" aria-hidden="true">
  <path d="M210 60 Q300 70 345 110 M425 110 Q500 90 560 60 M640 60 Q730 70 775 110 M855 110 Q920 140 990 60" fill="none" stroke="#d9a3a6" stroke-width="1.5" stroke-dasharray="2 4"/>
</svg>
<div class="step-num" style="left:127px;top:799px">1</div>
<div class="step-num" style="left:343px;top:852px">2</div>
<div class="step-num" style="left:557px;top:799px">3</div>
<div class="step-num" style="left:772px;top:852px">4</div>
<div class="step-num" style="left:987px;top:799px">5</div>
<p class="step-text" style="left:74px;top:912px">Artists and venues sign up for free and create a profile</p>
<p class="step-text" style="left:290px;top:964px">Venues search for an artist for their upcoming gigs</p>
<p class="step-text" style="left:504px;top:912px">Venues request a quote and communicate with the artist direct</p>
<p class="step-text" style="left:719px;top:964px">The gig is booked in once payment is provided by the venue.</p>
<p class="step-text" style="left:934px;top:912px">Upon completion the money is paid to the artist within 48 hours or less.</p>

<section class="why">
  <h2 class="section-title" style="top:47px;color:var(--red)">Why <span class="light">TuneRoost?</span></h2>
</section>
<div class="why-badge" role="img" aria-label="Round badge with crowd at a concert"></div>
<div class="why-item">
  <h3 style="left:237px;top:1248px">Simple</h3>
  <p class="right" style="left:72px;top:1289px">TuneRoost makes gig booking easy for both the venue and artist.</p>
  <h3 style="left:223px;top:1394px">Connect</h3>
  <p class="right" style="left:72px;top:1435px">Join the TuneRoost community which is full of amazing artists and venues.</p>
  <h3 style="left:898px;top:1248px">Protection</h3>
  <p style="left:898px;top:1289px">Everyone is protected with our complimentary dispute resolutions</p>
  <h3 style="left:898px;top:1394px">Price</h3>
  <p style="left:898px;top:1435px">Get the best rate possible with TuneRoost only receiving 5% of the artists fee</p>
</div>
<div class="why-icon" style="left:328px;top:1255px"><svg width="22" height="24" viewBox="0 0 22 24"><rect x="3" y="1" width="16" height="22" rx="2" fill="var(--red)"/><path d="M7 7h8M7 11h8M7 15h8" stroke="#1d1d1d" stroke-width="1.6"/></svg></div>
<div class="why-icon" style="left:328px;top:1401px"><svg width="24" height="24" viewBox="0 0 24 24" fill="var(--red)"><circle cx="18" cy="5" r="3.5"/><circle cx="6" cy="12" r="3.5"/><circle cx="18" cy="19" r="3.5"/><path d="M6 12L18 5M6 12l12 7" stroke="var(--red)" stroke-width="2"/></svg></div>
<div class="why-icon" style="left:812px;top:1255px"><svg width="20" height="24" viewBox="0 0 20 24"><path d="M5 11V7a5 5 0 0110 0v4" fill="none" stroke="var(--red)" stroke-width="2.4"/><rect x="2" y="10" width="16" height="12" rx="2" fill="var(--red)"/><circle cx="10" cy="16" r="2" fill="#1d1d1d"/></svg></div>
<div class="why-icon" style="left:812px;top:1401px"><svg width="24" height="24" viewBox="0 0 24 24"><path d="M12 2h9v9L11 21 2 12z" fill="var(--red)"/><circle cx="16.5" cy="6.5" r="1.8" fill="#1d1d1d"/></svg></div>

<section class="feature">
  <svg class="frame" style="left:77px;top:1692px;background:none" width="416" height="416" aria-hidden="true"><polygon points="0,0 416,0 0,416" fill="var(--red)"/></svg>
  <div class="photo" role="img" aria-label="Crowd with raised hands in front of a red-lit concert stage" style="left:98px;top:1713px;width:416px;height:416px;background:radial-gradient(ellipse 200px 160px at 200px 150px,#f08080 0%,#d8373a 50%,transparent 80%),linear-gradient(180deg,#c8262a 0%,#9a1518 55%,#2a0608 85%,#120204 100%)"></div>
  <h2 style="left:630px;top:1712px">Venues</h2>
  <ul class="bullets" style="left:630px;top:1765px">
    <li>TuneRoost is a 100% FREE service for all venues - you pay us nothing!</li>
    <li>Get instant access to hundreds of artists around your local community</li>
    <li>All genres to suit any venue from a pub to a wedding or even a nightclub</li>
    <li>Simple booking process with a money back guarantee</li>
    <li>Communicate directly with the artist and negotiate the price</li>
  </ul>
  <p class="body-copy" style="left:630px;top:1974px;width:490px">TuneRoost is not yet ready to host gigs as we're currently working on building our artists. We are launching for venues in Q4 2019. Pre-register now to keep informed and be one of the first people to use our platform.</p>
  <div class="pill-form" style="left:629px;top:2075px;width:393px"><span class="ph">Enter your email</span><span class="btn">REGISTER</span></div>

  <h2 style="left:80px;top:2253px">Artists</h2>
  <ul class="bullets" style="left:78px;top:2306px">
    <li>Sign up to TuneRoost for FREE and get yourself in front of venues</li>
    <li>Only pay us if you get a gig - we only get 5% of the fee you charge the venue</li>
    <li>All genres and artists welcome - as long as you're experienced and professional</li>
    <li>Get paid within 48 hours or less after the gig guaranteed!</li>
    <li>Negotiate your price and don't pay huge agent fees to ensure you earn top dollar</li>
  </ul>
  <p class="abs red" style="left:80px;top:2585px;font-size:13px">Sign up and create your TuneRoost profile now</p>
  <div class="pill-form" style="left:78px;top:2633px;width:394px"><span class="ph">Enter your email</span><span class="btn">REGISTER</span></div>
  <svg class="abs" style="left:706px;top:2244px" width="417" height="418" aria-hidden="true"><polygon points="0,0 417,0 417,418" fill="var(--red)"/></svg>
  <div class="photo" role="img" aria-label="Musician playing acoustic guitar at a microphone on a softly lit stage" style="left:686px;top:2265px;width:416px;height:416px;background:radial-gradient(ellipse 180px 160px at 160px 180px,#e0a0c0 0%,transparent 70%),linear-gradient(135deg,#c080b8 0%,#8a3d7a 40%,#5a2850 70%,#2c1430 100%)"></div>
</section>

<section class="about">
  <h2>About <span class="light">TuneRoost?</span></h2>
  <p class="intro">Lorem Ipsum is simply dummy text of the printing and typesetting industry. Lorem Ipsum has been the industry's standard dummy text ever since the 1500s, when an unknown printer took a galley.</p>
  <p class="more">Lorem Ipsum is simply dummy text of the printing and typesetting industry. Lorem Ipsum has been the industry's standard dummy text ever since the 1500s, when an unknown printer took a galley of type and scrambled it to make a type specimen book. It has survived not only five centuries, but also the leap into electronic typesetting, remaining essentially unchanged. It was popularised in the 1960s with the release of Letraset sheets containing.</p>
</section>

<h2 class="section-title" style="top:3100px">Get In <span class="light">Touch</span></h2>
<div class="field" style="left:77px;top:3173px;width:333px;height:46px">Name</div>
<div class="field" style="left:433px;top:3173px;width:333px;height:46px">Phone</div>
<div class="field" style="left:790px;top:3173px;width:332px;height:46px">Email</div>
<div class="field" style="left:77px;top:3245px;width:1045px;height:92px;border-radius:30px">Message</div>
<div class="submit">SUBMIT</div>

<footer class="footer">
  <svg class="abs" style="left:568px;top:56px" width="64" height="56" viewBox="0 0 64 56" aria-hidden="true">
    <path d="M2 18l18-6 24 6 18-6v38l-18 6-24-6-18 6z" fill="var(--red)"/>
    <path d="M32 4a11 11 0 0111 11c0 8-11 20-11 20S21 23 21 15A11 11 0 0132 4z" fill="var(--red)" stroke="#1d1d1d" stroke-width="2.5"/>
    <circle cx="32" cy="15" r="4" fill="#1d1d1d"/>
  </svg>
  <p class="blurb">Lorem Ipsum is simply dummy text of the<br>printing and typesetting industry.</p>
  <div class="call"><span>CALL US ON</span><span class="ring"><svg width="22" height="22" viewBox="0 0 24 24"><path d="M6.6 10.8a15 15 0 006.6 6.6l2.2-2.2a1 1 0 011-.25 11.4 11.4 0 003.6.57 1 1 0 011 1V20a1 1 0 01-1 1A17 17 0 013 4a1 1 0 011-1h3.5a1 1 0 011 1c0 1.25.2 2.45.57 3.57a1 1 0 01-.25 1z" fill="var(--red)"/></svg></span><span>123 456 7899</span></div>
</footer>
<div class="copyright">©TuneRoost. 2019 - All Rights Reserved.</div>

</body>
</html>
```